Website Design - TallyPorchHelpers.net

PLEASE CHECK WORD DOCUMENT ATTACHED FOR WEBSITE FLOW.

Target Market(s)

REAL ESTATE AGENTS ARE THE TARGET MARKET

Industry/Entity Type

Real Estate

Coding

Coded - Design and coding required

Number of Pages Required

4 page

Colors

Designer to choose colors to be used in the design.

Requirements
Must have
• WE LIKE RED LOGO ATTACHED
Nice to have
• PLEASE CHECK WORD DOCUMENT ATTACHED FOR WEBSITE FLOW.
Should not have

```html
<!DOCTYPE html>
<html lang="en">
<head>
<meta charset="utf-8">
<title>TallyPorchHelpers.net</title>
<link href="https://fonts.googleapis.com/css2?family=Roboto:wght@400;500;700;900&display=swap" rel="stylesheet">
<style>
:root{
  --red:#d0202a;
  --red-dark:#a9151e;
  --navy:#272b7a;
  --navy-dark:#1c1f5e;
  --ink:#2a2a33;
  --muted:#6d6d78;
  --light:#f3f3f6;
  --line:#dadbe3;
  --footer:#1f1f26;
  --footer-text:#c9c9d2;
  --white:#ffffff;
}
*{box-sizing:border-box;margin:0;padding:0}
html,body{width:1200px;height:5310px;overflow:hidden}
body{position:relative;background:var(--white);font-family:"Roboto",Arial,sans-serif;color:var(--ink)}
.abs{position:absolute}
.center{text-align:center}
h2.section-title{font-size:34px;font-weight:700;color:var(--ink);text-transform:uppercase;letter-spacing:1px;line-height:1.35}
h2.section-title.on-dark{color:var(--white)}

/* top bar + header */
.topbar{left:500px;top:0;width:700px;height:30px;background:var(--red);color:var(--white);font-size:11px;display:flex;align-items:center;gap:30px;padding-left:56px}
.topbar .search{margin-left:auto;margin-right:40px;width:160px;height:18px;background:var(--white);border-radius:2px}
.header{left:0;top:30px;width:1200px;height:95px;background:var(--white);border-bottom:1px solid var(--line)}
.brand{left:134px;top:24px;display:flex;align-items:center;gap:10px;font-size:22px;font-weight:900;color:var(--red)}
.brand .mark{width:30px;height:30px;background:var(--red)}
.nav{right:120px;top:42px;display:flex;gap:46px;font-size:13px;font-weight:700;color:var(--ink);text-transform:uppercase}

/* hero */
.hero{left:0;top:125px;width:1200px;height:600px;background:linear-gradient(180deg,#7d8790 0%,#5f6e5a 45%,#3f5a33 100%)}
.hero-curve{left:0;top:650px;width:1200px;height:150px}
.dots{display:flex;gap:8px}
.dots span{width:11px;height:11px;border-radius:50%;border:2px solid #9a9aa8;background:transparent}
.dots span.on{background:#9a9aa8}

/* options */
.options{left:0;top:855px;width:1200px}
.option-row{left:0;top:970px;width:1200px;display:flex;justify-content:center;gap:24px}
.pill{height:40px;padding:0 26px;border:2px solid var(--red);border-radius:20px;display:flex;align-items:center;font-size:13px;font-weight:700;color:var(--red);text-transform:uppercase}
.pill.active{background:var(--red);color:var(--white)}

/* steps */
.steps-title{left:0;top:1085px;width:1200px}
.steps-sub{left:0;top:1136px;width:1200px;font-size:13px;letter-spacing:4px;color:var(--muted)}
.step{top:1205px;width:260px;text-align:center}
.step .num{width:110px;height:110px;margin:0 auto;border:3px solid #c7c8d2;border-radius:50%;display:flex;align-items:center;justify-content:center;font-size:60px;font-weight:900;color:var(--navy)}
.step p{margin-top:32px;font-size:13px;line-height:1.6;color:var(--muted)}

/* pricing */
.pricing-band{left:0;top:1543px;width:1200px;height:160px;background:var(--navy)}
.pricing-title{left:0;top:1602px;width:1200px}
.cards{left:0;top:1680px;width:1200px;display:flex;gap:12px;padding:0 2px}
.card{width:230px;height:480px;background:var(--white);border:1px solid var(--line);position:relative}
.badge{width:84px;height:84px;margin:24px auto 0;border-radius:50%;background:var(--navy);border:4px solid #c6c8e4;color:var(--white);display:flex;flex-direction:column;align-items:center;justify-content:center;font-weight:900;font-size:26px;line-height:1}
.badge small{font-size:11px;font-weight:700;margin-top:3px}
.price{margin-top:24px;height:44px;background:var(--red);color:var(--white);display:flex;align-items:center;justify-content:center;font-size:26px;font-weight:700}
.price.quote{font-size:10px;letter-spacing:.3px}
.card ul{list-style:none;padding:18px 18px 0}
.card li{font-size:11px;line-height:1.5;color:var(--muted);margin-bottom:14px;padding-left:16px;position:relative}
.card li::before{content:"";position:absolute;left:0;top:4px;width:7px;height:7px;border-radius:50%;background:var(--red)}
.buy{margin:8px 0 0 18px;width:100px;height:28px;background:var(--navy);color:var(--white);font-size:11px;font-weight:700;display:flex;align-items:center;justify-content:center}
.card .note{padding:14px 18px 0;font-size:11px;line-height:1.5;color:var(--muted)}

/* free services */
.services-title{left:0;top:2272px;width:1200px}
.service{top:2435px;width:240px;text-align:center}
.service .icon{width:108px;height:108px;margin:0 auto;border-radius:50%;background:var(--red);display:flex;align-items:center;justify-content:center}
.service h3{margin-top:22px;font-size:20px;font-weight:700;color:var(--navy)}
.service p{margin-top:10px;font-size:12px;line-height:1.6;color:var(--muted)}

/* service area */
.map{left:0;top:2850px;width:1200px;height:530px;background:linear-gradient(160deg,#dfe3e8 0%,#cfd8c8 45%,#c9cfd9 100%)}
.area-box{left:248px;top:2807px;width:700px;height:140px;background:var(--white);box-shadow:0 4px 14px rgba(0,0,0,.15);padding:22px 40px}
.area-box h2{text-align:center;font-size:32px;font-weight:700;color:var(--ink)}
.area-input{margin-top:18px;height:40px;border:1px solid var(--line);border-radius:20px;display:flex;align-items:center;padding:0 4px 0 20px;font-size:11px;color:#9a9aa5}
.area-input .go{margin-left:auto;width:34px;height:34px;border-radius:50%;background:var(--red);display:flex;align-items:center;justify-content:center}

/* faq */
.faq-title{left:0;top:3480px;width:1200px}
.faq{left:276px;top:3562px;width:652px}
.faq-open{height:38px;background:var(--red);color:var(--white);font-size:13px;font-weight:500;display:flex;align-items:center;justify-content:space-between;padding:0 12px 0 16px}
.faq-answer{padding:16px;font-size:12px;line-height:1.6;color:var(--muted);border:1px solid var(--line);border-top:0}
.faq-item{margin-top:10px;height:32px;border-bottom:1px solid var(--line);display:flex;align-items:center;justify-content:space-between;padding-left:16px;font-size:12px;color:var(--muted)}
.toggle{width:32px;height:32px;background:var(--red);color:var(--white);display:flex;align-items:center;justify-content:center;font-weight:700;font-size:16px}
.toggle.minus{width:22px;height:22px;background:transparent;border:1px solid var(--white)}

/* testimonials */
.testi-band{left:0;top:3940px;width:1200px;height:540px}
.testi-title{left:0;top:4093px;width:1200px}
.quote{top:4195px;width:300px;display:flex;gap:16px;color:var(--white)}
.avatar{flex:none;width:70px;height:70px;border-radius:50%;background:linear-gradient(135deg,#e7c9b5,#9b7b68);border:3px solid var(--white)}
.quote p{font-size:11px;line-height:1.6;opacity:.9}
.quote b{display:block;margin-top:10px;font-size:12px}
.quote span{font-size:10px;opacity:.8}
.testi-dots{left:0;top:4376px;width:1200px;justify-content:center}
.testi-dots span{border-color:var(--white)}
.testi-dots span.on{background:var(--white)}

/* contact */
.contact-bg{left:0;top:4480px;width:1200px;height:230px;background:var(--light)}
.contact{left:131px;top:4496px;width:938px;height:336px;background:var(--white);box-shadow:0 6px 18px rgba(0,0,0,.12);padding:26px 70px}
.contact h2{text-align:center;font-size:32px;font-weight:700;color:var(--navy)}
.form{display:flex;gap:30px;margin-top:26px}
.form .col{flex:1}
.field{height:36px;border:1px solid var(--line);margin-bottom:14px;font-size:11px;color:#9a9aa5;padding:11px 12px}
.field.area{height:136px}
.submit{margin:8px auto 0;width:220px;height:38px;background:var(--navy);color:var(--white);font-size:13px;font-weight:700;display:flex;align-items:center;justify-content:center}

/* footer */
.footer{left:0;top:4710px;width:1200px;height:600px;background:var(--footer)}
.fcol{top:4910px;color:var(--footer-text)}
.fcol h4{font-size:20px;font-weight:700;color:var(--white);text-transform:uppercase;line-height:1.3;margin-bottom:20px}
.fcol p{font-size:12px;line-height:1.7;color:var(--footer-text)}
.fline{display:flex;gap:12px;align-items:flex-start;font-size:12px;line-height:1.5;margin-bottom:14px;color:var(--footer-text)}
.fline i{flex:none;width:14px;height:14px;border-radius:50%;background:var(--red);margin-top:2px}
.links{list-style:none;font-size:12px;line-height:2;color:var(--footer-text)}
.links li::before{content:"›  ";color:var(--red)}
.fbrand{left:903px;top:4945px;display:flex;align-items:center;gap:10px;font-size:20px;font-weight:900;color:var(--white)}
.fbrand .mark{width:26px;height:26px;background:var(--white)}
.socials{left:930px;top:5020px;display:flex;gap:10px}
.socials span{width:26px;height:26px;border-radius:50%;border:1px solid #8b8b96}
.copy{left:0;top:5222px;width:1200px;font-size:11px;color:#9a9aa5;text-align:center;line-height:2}

/* overlay + modal */
.overlay{left:0;top:0;width:1200px;height:5310px;background:rgba(15,15,25,.5);z-index:50}
.modal{left:212px;top:248px;width:776px;height:325px;background:var(--white);z-index:60;display:flex}
.modal-copy{width:440px;padding:36px 34px;text-align:center}
.modal-icon{width:48px;height:48px;margin:0 auto;border-radius:50%;background:var(--red);border:4px solid #f2c3c6;display:flex;align-items:center;justify-content:center}
.modal-copy h3{margin-top:14px;font-size:30px;font-weight:500;line-height:1.1}
.modal-copy h2{font-size:34px;font-weight:700;text-transform:uppercase;line-height:1.15}
.modal-copy p{margin-top:8px;font-size:13px;color:var(--muted)}
.signup{margin-top:26px;height:38px;border:1px solid var(--line);border-radius:19px;display:flex;align-items:center;padding:0 3px 0 16px;font-size:11px;color:#9a9aa5}
.signup .btn{margin-left:auto;height:30px;padding:0 18px;border-radius:15px;background:var(--red);color:var(--white);font-size:12px;font-weight:700;display:flex;align-items:center}
.modal-photo{flex:1;background:linear-gradient(135deg,#eef1f5 0%,#bcc6d2 55%,#33405a 100%)}
.close{right:12px;top:12px;width:22px;height:22px;border-radius:50%;border:1px solid #888;background:var(--white);font-size:12px;display:flex;align-items:center;justify-content:center;color:#555}
</style>
</head>
<body>

<div class="abs topbar"><span>Call Us Now! +1 (555) 014-2290</span><span>hello@tallyporchhelpers.net</span><div class="search"></div></div>
<header class="abs header">
  <div class="abs brand"><span class="mark"></span>TallyPorchHelpers.net</div>
  <nav class="abs nav"><span>How It Works</span><span>Service Area</span><span>Pricing</span><span>About Us</span><span>FAQ</span></nav>
</header>

<div class="abs hero" role="img" aria-label="Photo of a suburban home with an open house sign on the lawn"></div>
<svg class="abs hero-curve" viewBox="0 0 1200 150" preserveAspectRatio="none">
  <path d="M0 0H1200V100Q600 200 0 100Z" fill="#272b7a"/>
  <path d="M0 0H1200V70Q600 170 0 70Z" fill="#1c1f5e"/>
  <path d="M0 0H1200V40Q600 140 0 40Z" fill="#3f5a33"/>
</svg>
<div class="abs dots" style="left:572px;top:752px"><span class="on"></span><span></span><span></span></div>

<section>
  <h2 class="abs section-title center options">Choose the option below that<br>best describes you</h2>
  <div class="abs option-row">
    <div class="pill">I'm a full on brokerage</div>
    <div class="pill active">I'm an indie broker with a team</div>
    <div class="pill">I need sign placement ASAP</div>
  </div>
</section>

<section>
  <h2 class="abs section-title center steps-title">How it works?</h2>
  <div class="abs center steps-sub">3 EASY STEPS</div>
  <div class="abs step" style="left:153px"><div class="num">1</div><p>We travel the routes to your listing, place strong directional<br>signage and confirm each spot so buyers<br>find your open house.</p></div>
  <div class="abs step" style="left:472px"><div class="num">2</div><p>We check signs during the event<br>and keep every route clear.</p></div>
  <div class="abs step" style="left:790px"><div class="num">3</div><p>We pick up the signs once the open house<br>wraps up.</p></div>
</section>

<section>
  <div class="abs pricing-band"></div>
  <h2 class="abs section-title on-dark center pricing-title">Pricing</h2>
  <div class="abs cards">
    <div class="card"><div class="badge">5<small>SIGNS</small></div><div class="price">$49</div><ul><li>Place signs strategically at main routes leading to your listing</li><li>Pick up the signs after the open house</li><li>Send a photo report to your inbox</li></ul><div class="buy">BUY NOW</div><p class="note">Sign up for a subscription to receive our marketing services for free.</p></div>
    <div class="card"><div class="badge">10<small>SIGNS</small></div><div class="price">$59</div><ul><li>Place signs strategically at main routes leading to your listing</li><li>Pick up the signs after the open house</li><li>Send a photo report to your inbox</li></ul><div class="buy">BUY NOW</div><p class="note">Sign up for a subscription to receive our marketing services for free.</p></div>
    <div class="card"><div class="badge">15<small>SIGNS</small></div><div class="price">$69</div><ul><li>Place signs strategically at main routes leading to your listing</li><li>Pick up the signs after the open house</li><li>Send a photo report to your inbox</li></ul><div class="buy">BUY NOW</div><p class="note">Sign up for a subscription to receive our marketing services for free.</p></div>
    <div class="card"><div class="badge">20<small>SIGNS</small></div><div class="price">$79</div><ul><li>Place signs strategically at main routes leading to your listing</li><li>Pick up the signs after the open house</li><li>Send a photo report to your inbox</li></ul><div class="buy">BUY NOW</div><p class="note">Sign up for a subscription to receive our marketing services for free.</p></div>
    <div class="card"><div class="badge">25+<small>SIGNS</small></div><div class="price quote">CONTACT US FOR A CUSTOM QUOTE</div><ul><li>Place signs strategically at main routes leading to your listing</li><li>Pick up the signs after the open house</li><li>Send a photo report to your inbox</li></ul><div class="buy">BUY NOW</div><p class="note">Sign up for a subscription to receive our marketing services for free.</p></div>
  </div>
</section>

<section>
  <h2 class="abs section-title center services-title">Sign up for a subscription and get these<br>marketing services for free</h2>
  <div class="abs service" style="left:107px">
    <div class="icon"><svg width="50" height="46" viewBox="0 0 50 46"><path d="M4 4H46V32H20L10 42V32H4Z" fill="none" stroke="#fff" stroke-width="4" stroke-linejoin="round"/><circle cx="15" cy="18" r="3" fill="#fff"/><circle cx="25" cy="18" r="3" fill="#fff"/><circle cx="35" cy="18" r="3" fill="#fff"/></svg></div>
    <h3>SMS</h3><p>Send text blasts to your neighborhood<br>announcing your open house so<br>locals know the date and time<br>of every showing.</p>
  </div>
  <div class="abs service" style="left:358px">
    <div class="icon"><svg width="52" height="38" viewBox="0 0 52 38"><rect x="3" y="3" width="46" height="32" rx="2" fill="none" stroke="#fff" stroke-width="4"/><path d="M4 5L26 22L48 5" fill="none" stroke="#fff" stroke-width="4"/></svg></div>
    <h3>EMAIL</h3><p>Email blasts to your neighborhood<br>announcing your open house so<br>locals know the date and time<br>of every showing.</p>
  </div>
  <div class="abs service" style="left:606px">
    <div class="icon"><svg width="46" height="46" viewBox="0 0 46 46"><rect x="3" y="3" width="40" height="40" rx="6" fill="none" stroke="#fff" stroke-width="4"/><path d="M12 30L23 14L34 30" fill="none" stroke="#fff" stroke-width="4" stroke-linejoin="round"/></svg></div>
    <h3>FB AD</h3><p>Targeted social ads that promote<br>your open house locally.</p>
  </div>
  <div class="abs service" style="left:854px">
    <div class="icon"><svg width="48" height="48" viewBox="0 0 48 48"><path d="M4 4H24L44 24L24 44L4 24Z" fill="none" stroke="#fff" stroke-width="4" stroke-linejoin="round"/><circle cx="15" cy="15" r="4" fill="#fff"/></svg></div>
    <h3>VB</h3><p>Voice blasts to your neighborhood<br>announcing your open house so<br>locals know about the<br>upcoming event.</p>
  </div>
</section>

<section>
  <div class="abs map" role="img" aria-label="Map of the service area along the coast"></div>
  <div class="abs area-box">
    <h2>SERVICE AREA</h2>
    <div class="area-input">Enter your zip code to check if we serve your area<div class="go"><svg width="16" height="16" viewBox="0 0 16 16"><path d="M1 8L15 1L10 15L8 9Z" fill="#fff"/></svg></div></div>
  </div>
</section>

<section>
  <h2 class="abs section-title center faq-title">FAQs</h2>
  <div class="abs faq">
    <div class="faq-open">What is open house? <span class="toggle minus">–</span></div>
    <p class="faq-answer">An open house is a scheduled time when a home for sale is open for buyers to walk through. We place clear directional signs along nearby streets so visitors can find it easily, then collect them afterwards.</p>
    <div class="faq-item">Why do we need it?<span class="toggle">+</span></div>
    <div class="faq-item">Where do I sign up?<span class="toggle">+</span></div>
    <div class="faq-item">What's more to know on it?<span class="toggle">+</span></div>
    <div class="faq-item">What is open house?<span class="toggle">+</span></div>
  </div>
</section>

<section>
  <svg class="abs testi-band" viewBox="0 0 1200 540" preserveAspectRatio="none">
    <path d="M0 60Q300 0 600 40T1200 30V540H0Z" fill="#d0202a"/>
  </svg>
  <h2 class="abs section-title on-dark center testi-title">What our clients say</h2>
  <div class="abs quote" style="left:130px"><div class="avatar" role="img" aria-label="Client portrait"></div><div><p>“The team placed our signs early and the turnout doubled. Reliable, quick and easy to book for every open house we run.”</p><b>Dana Whitlow</b><span>Listing Agent, Bayview</span></div></div>
  <div class="abs quote" style="left:456px"><div class="avatar" role="img" aria-label="Client portrait"></div><div><p>“The team placed our signs early and the turnout doubled. Reliable, quick and easy to book for every open house we run.”</p><b>Marcus Reyes</b><span>Broker, Hillcrest</span></div></div>
  <div class="abs quote" style="left:789px"><div class="avatar" role="img" aria-label="Client portrait"></div><div><p>“The team placed our signs early and the turnout doubled. Reliable, quick and easy to book for every open house we run.”</p><b>Priya Halden</b><span>Realtor, Lakeside</span></div></div>
  <div class="abs dots testi-dots"><span class="on"></span><span></span><span></span><span></span></div>
</section>

<div class="abs contact-bg"></div>
<footer class="abs footer"></footer>
<section class="abs contact">
  <h2>CONTACT US RIGHT NOW!</h2>
  <div class="form">
    <div class="col"><div class="field">Name</div><div class="field">Email</div><div class="field">Phone</div></div>
    <div class="col"><div class="field area">Message</div></div>
  </div>
  <div class="submit">SUBMIT</div>
</section>

<div class="abs fcol" style="left:131px;width:300px"><h4>About<br>TallyPorchHelpers.net</h4><p>TallyPorchHelpers.net is a friendly team that<br>places directional signs for open houses, so<br>agents can focus on buyers while we take<br>care of the streets, the timing and the<br>pickup once the event is done.</p></div>
<div class="abs fcol" style="left:489px;width:220px"><h4>Contact Us</h4>
  <div class="fline"><i></i><span>1420 Harbor Lane<br>Suite 8, Springfield</span></div>
  <div class="fline"><i></i><span>Phone: +1 (555) 014-2290</span></div>
  <div class="fline"><i></i><span>hello@tallyporchhelpers.net</span></div>
  <div class="fline"><i></i><span>Mon – Sat: 8am – 6pm</span></div>
</div>
<div class="abs fcol" style="left:736px"><h4>Quick Links</h4><ul class="links"><li>How It Works</li><li>Service Area</li><li>Pricing</li><li>About Us</li><li>FAQ</li></ul></div>
<div class="abs fbrand"><span class="mark"></span>TallyPorchHelpers.net</div>
<div class="abs socials"><span></span><span></span><span></span><span></span></div>
<div class="abs copy">Copyright 2024 TallyPorchHelpers.net. All Rights Reserved.<br>Terms and Conditions | Privacy Policy</div>

<div class="abs overlay"></div>
<div class="abs modal">
  <div class="modal-copy">
    <div class="modal-icon"><svg width="20" height="15" viewBox="0 0 20 15"><rect x="1" y="1" width="18" height="13" fill="none" stroke="#fff" stroke-width="2"/><path d="M1 2L10 9L19 2" fill="none" stroke="#fff" stroke-width="2"/></svg></div>
    <h3>Subscribe To</h3>
    <h2>Our Newsletter</h2>
    <p>Stay up to date with the latest news.</p>
    <div class="signup">Enter Email<span class="btn">SUBSCRIBE</span></div>
  </div>
  <div class="modal-photo" role="img" aria-label="Photo of two business people reviewing a tablet"></div>
  <div class="abs close">×</div>
</div>

</body>
</html>
```